Puffy Clouds Cotton Candy

Looking for a logo design and business cards to help a 13 year old entrepreneur promote her cotton candy business.
Contact Information for Business Card
Name, Phone & Email
Colors
E54698
E96AAD
F1A4CE
F9D9EA
FCEFF6
A7469A
B969AE
D3A5CF
EDDBEB
F8F0F9
6B429C
8869AF
B7A5CE
E3DAEB
F3F0F8
Requirements
Must have
- A fun feel that is appropriate for a teenage girl selling cotton candy

```html
<!DOCTYPE html>
<html lang="en">
<head>
<meta charset="utf-8">
<title>Puffy Clouds Cotton Candy – Business Card</title>
<link rel="stylesheet" href="https://fonts.googleapis.com/css2?family=Montserrat:wght@500;700&display=swap">
<style>
  :root {
    --backdrop: #2b2b2e;
    --grape: #6b429c;
    --candy-pink: #e54698;
    --emboss-pink: #f14fa5;
    --emboss-shade: #d63f8c;
    --white: #ffffff;
  }
  * { margin: 0; padding: 0; box-sizing: border-box; }
  html, body {
    width: 1200px; height: 1015px; overflow: hidden;
    background: var(--backdrop);
    font-family: "Montserrat", sans-serif;
  }
  .canvas {
    position: relative; width: 1200px; height: 1015px;
  }
  .card {
    position: absolute; left: 250px; width: 700px; height: 400px;
    overflow: hidden;
  }
  .card--front { top: 70px; background: var(--grape); }
  .card--back { top: 545px; background: var(--candy-pink); }

  /* Front */
  .brand {
    position: absolute; inset: 0;
    display: flex; flex-direction: column; align-items: center; justify-content: center;
    gap: 22px;
  }
  .brand__dot {
    width: 120px; height: 120px; border-radius: 50%;
    border: 6px solid var(--candy-pink);
  }
  .brand__name {
    color: var(--candy-pink); font-weight: 700; font-size: 38px;
    line-height: 1.1; text-align: center;
  }

  /* Back */
  .contact {
    position: absolute; left: 78px; top: 150px; color: var(--white);
  }
  .contact__name { font-weight: 700; font-size: 26px; line-height: 1; }
  .contact__role { font-weight: 500; font-size: 15px; margin-top: 4px; }
  .contact__lines { margin-top: 24px; font-weight: 500; font-size: 15px; line-height: 1.35; }
  .contact__line { display: flex; align-items: center; gap: 8px; }
  .contact__line svg { width: 15px; height: 15px; flex: none; }
  .contact__address { margin-top: 26px; font-weight: 500; font-size: 15px; line-height: 1.35; }
  .emboss-ring {
    position: absolute; right: 40px; top: 34px; width: 330px; height: 330px;
  }
</style>
</head>
<body>
<main class="canvas">
  <section class="card card--front" aria-label="Card front">
    <div class="brand">
      <div class="brand__dot"></div>
      <p class="brand__name">Puffy Clouds<br>Cotton Candy</p>
    </div>
  </section>

  <section class="card card--back" aria-label="Card back">
    <div class="contact">
      <h1 class="contact__name">Lila Marsh</h1>
      <p class="contact__role">Managing Director</p>
      <div class="contact__lines">
        <p class="contact__line">
          <svg viewBox="0 0 24 24" aria-hidden="true"><path fill="#fff" d="M6.6 10.8a15 15 0 0 0 6.6 6.6l2.2-2.2c.3-.3.7-.4 1-.2 1.1.4 2.3.6 3.6.6.6 0 1 .4 1 1V20c0 .6-.4 1-1 1A17 17 0 0 1 3 4c0-.6.4-1 1-1h3.5c.6 0 1 .4 1 1 0 1.3.2 2.5.6 3.6.1.3 0 .7-.2 1z"/></svg>
          055-210 734 968
        </p>
        <p class="contact__line">
          <svg viewBox="0 0 24 24" aria-hidden="true"><path fill="#fff" d="M2 5h20v14H2zm2 2v.4l8 5.3 8-5.3V7zm0 2.8V17h16V9.8l-8 5.3z"/></svg>
          hello@puffyclouds.com
        </p>
      </div>
      <p class="contact__address">218, Meadow Lane Street<br>30814, Avalon Bay</p>
    </div>
    <svg class="emboss-ring" viewBox="0 0 330 330" aria-hidden="true">
      <circle cx="165" cy="165" r="155" fill="none" stroke="var(--emboss-shade)" stroke-width="12"/>
      <circle cx="165" cy="165" r="155" fill="none" stroke="var(--emboss-pink)" stroke-width="8"/>
    </svg>
  </section>
</main>
</body>
</html>
```